Tall ridge firewood

It a new firewood outlet in Jindabyne nsw that will only sell top hardwood firewood (ironbark , red gum, grey gum, an box mix. I would like to see a web page the we can do order online payment for delivery. It will all so need to have photos of the firewood. I all so have logo for tall ridge firewood
Must have a modem look but easy to use I would like to see a black back ground of some sort.

Here are some other firewood web pages for ideas and firewood info
http://www.example-logpile.com.au
http://www.example-stackwood.com.au
http://www.example-splitlog.com.au
http://www.example-kendaltimber.com.au/firewood

Industry/Entity Type

Firewood

```html
<!DOCTYPE html>
<html lang="en">
<head>
<meta charset="utf-8">
<title>Tall Ridge Firewood</title>
<link href="https://fonts.googleapis.com/css2?family=Anton&family=Open+Sans:wght@400;600;700&display=swap" rel="stylesheet">
<style>
:root{
  --bg:#141414;
  --bg-deep:#0c0c0c;
  --blue:#1a6fbf;
  --blue-dark:#135a9d;
  --white:#ffffff;
  --text:#e6e6e6;
  --muted:#bdbdbd;
  --line:#3a3a3a;
  --wood:#a8713f;
  --wood-dark:#5a3a1e;
}
*{box-sizing:border-box;margin:0;padding:0}
html,body{width:890px;height:1200px;overflow:hidden}
body{position:relative;background:radial-gradient(circle at 50% 30%,#1c1c1c,var(--bg-deep));font-family:"Open Sans",sans-serif;color:var(--text)}
.abs{position:absolute}
.display{font-family:"Anton",sans-serif;font-weight:400}

/* top nav */
.topbar{left:0;top:0;width:890px;height:27px;background:var(--white);border-bottom:3px solid var(--blue)}
.nav{left:277px;top:0;display:flex;height:27px;list-style:none}
.nav li{font-size:8.5px;font-weight:600;color:#555;text-transform:uppercase;padding:0 15px;line-height:27px;letter-spacing:.2px}
.nav li.active{background:var(--blue);color:var(--white);padding:0 20px}

/* brand */
.brand{left:98px;top:0;width:179px;height:147px;background:var(--white);border-radius:0 0 16px 16px;display:flex;flex-direction:column;align-items:center;justify-content:center;gap:8px}
.brand-mark{width:58px;height:58px;border-radius:50%;background:var(--blue)}
.brand-name{font-size:12px;font-weight:700;color:var(--blue);text-transform:uppercase}

/* contact */
.contact{font-size:8px;text-transform:uppercase;color:var(--text);display:flex;align-items:center;gap:5px}
.contact .big{font-family:"Anton",sans-serif;font-size:15px;color:var(--white)}
.contact a{color:var(--text)}
.search{left:359px;top:93px;width:193px;height:21px;border:1px solid #555;background:#1e1e1e;font-size:8.5px;color:#aaa;line-height:19px;padding-left:7px}
.search-btn{right:0;top:0;width:23px;height:19px;background:var(--blue)}
.order-btn{left:715px;top:94px;width:83px;height:19px;background:linear-gradient(#fff,#ddd);border-radius:2px;color:#222;font-size:8.5px;font-weight:600;text-align:center;line-height:19px}

/* hero */
.hero{left:98px;top:174px;width:700px;height:336px;background:#2b2b2b;border-radius:18px}
.hero-photo{left:104px;top:182px;width:687px;height:322px;border-radius:12px;background:radial-gradient(circle at 60% 45%,#c08a55,var(--wood) 45%,var(--wood-dark))}
.hero-arrow{width:34px;height:34px;background:rgba(20,20,20,.85);border-radius:5px;top:326px}
.hero-title{left:186px;top:312px;line-height:1.05}
.hero-title .l1{font-size:22px;color:#4a8fd6;display:block}
.hero-title .l2{font-size:30px;color:var(--white);display:block}

/* intro */
.h2{font-size:23px;color:var(--white);letter-spacing:.2px}
.body-copy{font-size:9.4px;line-height:11px;color:var(--text)}
.divider{width:1px;background:var(--line)}
.why-item{left:598px;display:flex;gap:13px;width:200px}
.tick{flex:none;width:16px;height:16px;background:#3d3d3d;border-radius:3px}
.btn-blue{background:var(--blue);color:var(--white);font-size:8.5px;text-align:center;line-height:19px;border-radius:2px;text-transform:uppercase}

/* products */
.products{left:98px;top:757px;width:700px;height:224px;background:var(--blue);border-radius:18px}
.products-rule{left:98px;top:802px;width:700px;height:1px;background:#4d8fd0}
.product-img{top:820px;width:142px;height:101px;border:2px solid #d9e4ef;border-radius:5px}
.product-name{top:935px;width:142px;text-align:center;font-size:10px;color:var(--white);text-transform:uppercase}
.product-price{top:948px;width:142px;text-align:center;font-size:13px;color:var(--white)}

/* footer */
.footer-rule{left:0;top:1022px;width:890px;height:1px;background:var(--line)}
.foot-h{top:1047px;font-size:8.5px;font-weight:700;color:var(--white);text-transform:uppercase}
.foot-list{list-style:none;top:1066px;font-size:8.4px;line-height:12.7px;color:var(--text)}
.foot-list li::before{content:"» ";}
.social{top:1068px;left:393px;display:flex;gap:4px}
.social span{width:21px;height:21px;display:block}
.copyright{left:0;top:1172px;width:890px;height:28px;background:var(--white);color:#333;font-size:8.6px;text-align:center;line-height:28px;text-transform:uppercase}
</style>
</head>
<body>

<div class="abs topbar"></div>
<ul class="abs nav">
  <li class="active">Home</li><li>About Us</li><li>Products</li><li>Accessories</li><li>Delivery</li><li>FAQ's</li><li>Contact Us</li>
</ul>

<div class="abs brand">
  <div class="brand-mark"></div>
  <div class="brand-name">Tall Ridge Firewood</div>
</div>

<div class="abs contact" style="left:428px;top:50px">
  <svg width="9" height="12" viewBox="0 0 9 12"><path d="M2 1 L4 3 L3 5 Q4 8 6 9 L8 8 L9 10 Q7 12 5 11 Q0 7 1 2 Z" fill="#bbb"/></svg>
  Call us - <span class="big">0400 317 882</span>
</div>
<div class="abs contact" style="left:588px;top:54px">
  <svg width="10" height="7" viewBox="0 0 10 7"><rect x=".5" y=".5" width="9" height="6" fill="none" stroke="#bbb"/><path d="M.5 .5 L5 4 L9.5 .5" fill="none" stroke="#bbb"/></svg>
  Email us - <a href="#">info@tallridgefirewood.example</a>
</div>

<div class="abs search">Find Firewood Products ..
  <div class="abs search-btn"><svg width="23" height="19" viewBox="0 0 23 19"><circle cx="11" cy="8.5" r="4" fill="none" stroke="#fff" stroke-width="1.6"/><path d="M14 11.5 L16.5 14" stroke="#fff" stroke-width="1.8"/></svg></div>
</div>
<div class="abs contact" style="left:588px;top:98px">
  <svg width="11" height="10" viewBox="0 0 11 10"><path d="M0 1 H2 L3.5 7 H9.5 L10.5 3 H3" fill="none" stroke="#bbb"/><circle cx="4" cy="9" r="1" fill="#bbb"/><circle cx="9" cy="9" r="1" fill="#bbb"/></svg>
  My cart - <span class="big" style="font-size:11px">0 item (s)</span>
</div>
<div class="abs order-btn">ORDER ONLINE</div>

<div class="abs hero"></div>
<div class="abs hero-photo" role="img" aria-label="Close-up photo of stacked hardwood firewood logs"></div>
<div class="abs hero-arrow" style="left:121px"><svg width="34" height="34" viewBox="0 0 34 34"><path d="M20 10 L13 17 L20 24" fill="none" stroke="#fff" stroke-width="3"/></svg></div>
<div class="abs hero-arrow" style="left:739px"><svg width="34" height="34" viewBox="0 0 34 34"><path d="M14 10 L21 17 L14 24" fill="none" stroke="#fff" stroke-width="3"/></svg></div>
<div class="abs hero-title display"><span class="l1">TOP HARDWOOD</span><span class="l2">FIREWOOD</span></div>

<h1 class="abs h2 display" style="left:98px;top:546px">Welcome to Tall Ridge Firewood</h1>
<div class="abs body-copy" style="left:98px;top:588px;width:420px">
  <p>Lorem ipsum dolor sit amet, consectetur adipisicing elit, sed do eiusmod tempor incididunt ut labore et dolore magna aliqua. Ut enim ad minim veniam, quis nostrud exercitation ullamco laboris nisi ut aliquip ex ea commodo consequat. Duis aute irure dolor in reprehenderit in voluptate velit esse cillum dolore eu fugiat nulla pariatur. Excepteur sint occaecat cupidatat non proident, sunt in culpa qui officia deserunt mollit anim id est laborum.</p>
  <p style="margin-top:11px">Lorem ipsum dolor sit amet, consectetur adipisicing elit, sed do eiusmod tempor incididunt ut labore et dolore magna aliqua. Ut enim ad minim veniam, quis nostrud exercitation ullamco laboris nisi ut aliquip ex ea commodo consequat. Duis aute irure dolor in reprehenderit in voluptate velit esse cillum dolore eu fugiat nulla pariatur. Excepteur sint occaecat cupidatat non proident, sunt in culpa qui officia deserunt mollit anim id est laborum.</p>
</div>
<div class="abs divider" style="left:555px;top:552px;height:168px"></div>

<h2 class="abs h2 display" style="left:600px;top:546px">Why Choose Us ?</h2>
<div class="abs why-item body-copy" style="top:589px"><span class="tick"><svg width="16" height="16" viewBox="0 0 16 16"><path d="M4 8 L7 11 L12 5" fill="none" stroke="#aaa" stroke-width="2"/></svg></span><span>Lorem ipsum dolor sit amet, consectetur adipisicing elit.</span></div>
<div class="abs why-item body-copy" style="top:624px"><span class="tick"><svg width="16" height="16" viewBox="0 0 16 16"><path d="M4 8 L7 11 L12 5" fill="none" stroke="#aaa" stroke-width="2"/></svg></span><span>Lorem ipsum dolor sit amet, consectetur adipisicing elit, sed do eiusmod tempor.</span></div>
<div class="abs why-item body-copy" style="top:659px"><span class="tick"><svg width="16" height="16" viewBox="0 0 16 16"><path d="M4 8 L7 11 L12 5" fill="none" stroke="#aaa" stroke-width="2"/></svg></span><span>Lorem ipsum dolor sit amet, consectetur adipisicing elit, sed do.</span></div>
<div class="abs btn-blue" style="left:601px;top:703px;width:69px">Read More</div>

<div class="abs products"></div>
<div class="abs products-rule"></div>
<h2 class="abs h2 display" style="left:133px;top:765px;font-size:21px">Our Products</h2>
<a class="abs" href="#" style="left:723px;top:774px;font-size:8.5px;color:#fff;font-weight:600">VIEW ALL</a>
<svg class="abs" style="left:110px;top:844px" width="14" height="52" viewBox="0 0 14 52"><path d="M12 2 L3 26 L12 50" fill="none" stroke="#cfe0f2" stroke-width="1.2"/></svg>
<svg class="abs" style="left:772px;top:844px" width="14" height="52" viewBox="0 0 14 52"><path d="M2 2 L11 26 L2 50" fill="none" stroke="#cfe0f2" stroke-width="1.2"/></svg>

<div class="abs product-img" style="left:134px;background:linear-gradient(#8a4a32,#5c3a2c 70%,#6d6d6d)" role="img" aria-label="Photo of split ironbark firewood in a trailer"></div>
<div class="abs product-name" style="left:134px">Ironbark</div>
<div class="abs product-price display" style="left:134px">$30.20 Only</div>

<div class="abs product-img" style="left:297px;background:linear-gradient(135deg,#9a3a28,#c4563d 50%,#6e2a1e)" role="img" aria-label="Photo of split red gum firewood"></div>
<div class="abs product-name" style="left:297px">Red Gum</div>
<div class="abs product-price display" style="left:297px">$30.20 Only</div>

<div class="abs product-img" style="left:458px;background:linear-gradient(135deg,#8c8a86,#5f5c58 50%,#9b9893)" role="img" aria-label="Photo of grey gum firewood logs"></div>
<div class="abs product-name" style="left:458px">Grey Gum</div>
<div class="abs product-price display" style="left:458px">$30.20 Only</div>

<div class="abs product-img" style="left:620px;background:radial-gradient(circle at 50% 55%,#e0602a,#3a1a10 45%,#1a1a1a 70%,#bbb)" role="img" aria-label="Photo of a box mix fire burning in a wood heater"></div>
<div class="abs product-name" style="left:620px">Box Mix</div>
<div class="abs product-price display" style="left:620px">$30.20 Only</div>

<div class="abs footer-rule"></div>
<div class="abs foot-h" style="left:98px">Navigation</div>
<ul class="abs foot-list" style="left:98px"><li>Home</li><li>About Us</li><li>Products</li><li>Accessories</li><li>Delivery</li><li>Faq`s</li><li>Contact Us</li></ul>
<div class="abs divider" style="left:206px;top:1049px;height:103px"></div>
<div class="abs foot-h" style="left:250px">Products</div>
<ul class="abs foot-list" style="left:250px"><li>Ironbark</li><li>Red gum</li><li>Grey gum</li><li>Box mix</li></ul>
<div class="abs divider" style="left:350px;top:1049px;height:103px"></div>
<div class="abs foot-h" style="left:393px">Follow us on</div>
<div class="abs social"><span style="background:#3b5b98"></span><span style="background:#1f9ed8"></span><span style="background:#1e7bb8"></span><span style="background:#d34836"></span></div>
<div class="abs divider" style="left:534px;top:1049px;height:103px"></div>
<div class="abs" style="left:572px;top:1043px;font-size:13px;font-weight:700;color:#fff">Happy Client`s</div>
<div class="abs body-copy" style="left:572px;top:1067px;width:230px">Lorem ipsum dolor sit amet, consectetur adipisicing elit, sed do eiusmod tempor incididunt ut labore et dolore magna aliqua.</div>
<div class="abs body-copy" style="left:572px;top:1110px"><b>Sam.</b> 15/06/13</div>
<div class="abs order-btn" style="left:573px;top:1136px;width:69px">READ MORE</div>

<div class="abs copyright">Copyright © <b>Tall Ridge Firewood</b> 2013. All right reserved.</div>

</body>
</html>
```